New Business Card Design Project

I need a design for business cards, i am an electrical business called "Corvane Electrical and Communications" i need the cards to be double sided with the company logo on the back (attached) the front needs to say my company name, web site, email address, telephone number, and ABN number and electrical license number. I am open to different arrangements of the information but would like the background to be incorporating something electrical or something that looks smart. open to all additional ideas also.

The company colours are orange and grey see logo attached.

Business Name: Corvane Electrical and Communications
Website: corvaneelectricalandcomms.example.com.au
Email: brent@corvaneelectricalandcomms.example.com.au
Telephone(mobile): 0481209736
ABN: 71208349162
Lic No: 418273D

Target Market(s)

Business entities, Project Managers, Accounts, Clients

Industry/Entity Type

Electrician

Contact Information for Business Card

I need a design for business cards, i am an electrical business called "Corvane Electrical and Communications" i need the cards to be double sided with the company logo on the back (attached) the front needs to say my company name

Font styles to use
Serif
Sans Serif

Colors
f37122
5c5c5c

Requirements
Must have
• Must have the Logo on the back open to different ways of it being on the back but had in mind to keep it central but again open to other options
Nice to have
• A real modern cool background that is eye catching yet contemporary
Should not have
• No backgrounds of a light bulb or plug or anything like that

```html
<!DOCTYPE html>
<html lang="en">
<head>
<meta charset="utf-8">
<title>Corvane Electrical and Communications – Business Cards</title>
<link rel="stylesheet" href="https://fonts.googleapis.com/css2?family=Open+Sans:wght@400;600;700&display=swap">
<style>
  :root {
    --canvas-bg: #3a3a3c;
    --card-black: #050505;
    --card-grey: #4a4c50;
    --orange: #f3a51f;
    --white: #ffffff;
    --text-light: #e8e8e8;
  }
  * { margin: 0; padding: 0; box-sizing: border-box; }
  html, body {
    width: 1200px; height: 900px; overflow: hidden;
    background: var(--canvas-bg);
    font-family: "Open Sans", Arial, sans-serif;
  }
  .canvas { position: relative; width: 1200px; height: 900px; }

  .card {
    position: absolute;
    width: 640px; height: 366px;
    border-radius: 22px;
    overflow: hidden;
    box-shadow: 0 18px 40px rgba(0,0,0,.45);
  }

  /* Back of card */
  .card-back { left: 80px; top: 70px; background: var(--card-black); }
  .card-back .brand {
    position: absolute; left: 0; right: 0; top: 120px;
    display: flex; align-items: center; justify-content: center; gap: 16px;
  }
  .brand-dot {
    width: 22px; height: 22px; border-radius: 50%;
    background: var(--orange); flex: none;
  }
  .brand-name {
    color: var(--white); font-weight: 600; line-height: 1.1;
    text-transform: uppercase; letter-spacing: 1px;
  }
  .card-back .brand-name { font-size: 34px; }
  .card-back .brand-name small { display: block; font-size: 19px; letter-spacing: 2px; }
  .card-back .website {
    position: absolute; left: 0; right: 0; bottom: 42px;
    text-align: center; font-size: 15px; color: var(--white);
  }
  .website .accent { color: var(--orange); }

  /* Front of card */
  .card-front { left: 480px; top: 470px; background: var(--card-grey); }
  .front-backdrop { position: absolute; inset: 0; }
  .card-front .brand {
    position: absolute; left: 32px; top: 150px;
    display: flex; align-items: center; gap: 10px;
  }
  .card-front .brand-dot { width: 18px; height: 18px; }
  .card-front .brand-name { font-size: 22px; }
  .card-front .brand-name small { display: block; font-size: 10.5px; letter-spacing: 1px; }

  .contact {
    position: absolute; left: 300px; top: 104px; width: 310px;
    color: var(--text-light);
  }
  .person-name {
    color: var(--orange); font-size: 26px; font-weight: 400;
    text-transform: uppercase; letter-spacing: .5px; line-height: 1.1;
  }
  .person-title { font-size: 12px; text-transform: uppercase; margin-bottom: 10px; color: var(--white); }
  .contact-list { list-style: none; font-size: 11px; line-height: 1.75; }
  .contact-list li { display: flex; align-items: center; gap: 7px; white-space: nowrap; }
  .contact-list svg { width: 11px; height: 11px; flex: none; }
  .label { color: var(--orange); font-weight: 600; }
  .reg { margin-top: 4px; font-size: 13px; line-height: 1.6; }
</style>
</head>
<body>
<main class="canvas">

  <section class="card card-back" aria-label="Business card back">
    <div class="brand">
      <span class="brand-dot"></span>
      <div class="brand-name">Corvane<small>Electrical &amp; Communications</small></div>
    </div>
    <p class="website">www.<span class="accent">corvaneelectricalandcomms</span>.example.com.au</p>
  </section>

  <section class="card card-front" aria-label="Business card front">
    <svg class="front-backdrop" viewBox="0 0 640 366" preserveAspectRatio="none" role="img" aria-label="Abstract backdrop of overlapping translucent teal squares">
      <defs>
        <linearGradient id="frontShade" x1="0" y1="1" x2="1" y2="0">
          <stop offset="0" stop-color="#27404b"/>
          <stop offset=".45" stop-color="#3c5561"/>
          <stop offset="1" stop-color="#55575b"/>
        </linearGradient>
      </defs>
      <rect width="640" height="366" fill="url(#frontShade)"/>
      <circle cx="470" cy="150" r="210" fill="none" stroke="#6a6c70" stroke-width="2" opacity=".45"/>
    </svg>

    <div class="brand">
      <span class="brand-dot"></span>
      <div class="brand-name">Corvane<small>Electrical &amp; Communications</small></div>
    </div>

    <div class="contact">
      <h1 class="person-name">Brent Maddox</h1>
      <p class="person-title">Director</p>
      <ul class="contact-list">
        <li>
          <svg viewBox="0 0 12 12"><path d="M2.5 1 L4.5 1 L5 3.5 L3.8 4.4 Q5 7 7.6 8.2 L8.5 7 L11 7.5 L11 9.5 Q11 11 9.5 11 Q1 10 1 2.5 Q1 1 2.5 1Z" fill="var(--orange)"/></svg>
          0481-209-736
        </li>
        <li>
          <svg viewBox="0 0 12 12"><rect x="1" y="2.5" width="10" height="7" fill="none" stroke="var(--orange)" stroke-width="1.3"/><path d="M1 2.5 L6 6.5 L11 2.5" fill="none" stroke="var(--orange)" stroke-width="1.3"/></svg>
          brent@corvaneelectricalandcomms.example.com.au
        </li>
        <li>
          <svg viewBox="0 0 12 12"><circle cx="6" cy="6" r="5" fill="none" stroke="var(--orange)" stroke-width="1.2"/><ellipse cx="6" cy="6" rx="2.2" ry="5" fill="none" stroke="var(--orange)" stroke-width="1"/><path d="M1 6 H11" stroke="var(--orange)" stroke-width="1"/></svg>
          www.corvaneelectricalandcomms.example.com.au
        </li>
      </ul>
      <p class="reg"><span class="label">ABN:</span> 71208349162<br><span class="label">Lic No:</span> 418273D</p>
    </div>
  </section>

</main>
</body>
</html>
```